Patent Law

Need to develop a home page for a patent lawyer.

Colors should go with logo, blues...

Company Name- Velun Tresk, PLLC

Company Overview-

I am an Intellectual Property Lawyer and focus on patents, copyrights, trademarks, & trade secrets. I work with small businesses and start ups in the chemical and biotech industries.

Why Us-

I am small firm that can provide large-firm service at a reasonable price. I also can charge flat-fees for entreprenuers in certain practice areas.

Services-
Intellectual Property
Patents
Copyrights
Trademarks
Trade secrets
Healthcare Compliance
Elder law
Wills
Trusts

Website we like-
http://www.quorvantlegal.example/ - within industry!!
http://www.daltrowemiko.example/
http://ulbrixtane.example/
http://thegravelcounsel.example/

Target Market(s)

My customers will be small business, specifically small start-up companies in the chemical and biotech arena.

Industry/Entity Type

Trade

Requirements
Must have
• Colors should go with logo, blues...

```html
<!DOCTYPE html>
<html lang="en">
<head>
<meta charset="utf-8">
<title>Velun Tresk, PLLC — Intellectual Property Law</title>
<link href="https://fonts.googleapis.com/css2?family=Arimo:wght@400;700&display=swap" rel="stylesheet">
<style>
:root{
  --blue:#0e87c8;
  --blue-deep:#0b6fa8;
  --ink:#5f5f5f;
  --nav:#7a7a7a;
  --rule:#dcdcdc;
  --white:#ffffff;
}
*{margin:0;padding:0;box-sizing:border-box}
html,body{width:1200px;height:1088px;overflow:hidden;background:var(--white);font-family:"Arimo",Arial,sans-serif;color:var(--ink)}
.page{position:relative;width:1200px;height:1088px}
.wrap{position:absolute;left:131px;width:938px}

.site-header{top:0;height:101px}
.brand{position:absolute;left:0;top:28px;display:flex;align-items:center;gap:8px}
.brand-dot{width:30px;height:30px;border-radius:50%;background:var(--blue)}
.brand-name{font-size:14px;font-weight:700;color:var(--blue-deep);letter-spacing:.5px;text-transform:uppercase}
.header-contact{position:absolute;right:0;top:19px;display:flex;align-items:center;gap:6px}
.phone{font-size:18px;color:var(--blue);margin-right:14px}
.map-link{font-size:13px;color:var(--nav)}
.main-nav{position:absolute;right:0;top:57px;display:flex;font-size:15px;color:var(--nav)}
.main-nav a{color:inherit;text-decoration:none;position:absolute;white-space:nowrap}
.main-nav .current{color:var(--blue);border-bottom:1px solid var(--blue);padding-bottom:2px}

.hero{top:101px;height:453px;overflow:hidden;border:1px solid #9a8f86;
  background:linear-gradient(90deg,#d9d4cf 0%,#cfc5bc 20%,#c89b72 50%,#b66a35 75%,#8c4d24 100%)}
.hero-photo{position:absolute;inset:0;background:radial-gradient(ellipse at 28% 45%,rgba(40,40,50,.55) 0,rgba(40,40,50,0) 40%),radial-gradient(ellipse at 92% 55%,rgba(80,60,40,.5) 0,rgba(80,60,40,0) 30%)}
.hero-caption{position:absolute;left:0;right:0;bottom:0;height:85px;background:rgba(20,20,24,.55);border-top:1px solid rgba(255,255,255,.25)}
.hero-caption p{position:absolute;left:23px;top:10px;font-size:18px;line-height:39px;color:var(--white);letter-spacing:-.3px}
.btn{position:absolute;right:19px;top:29px;width:143px;height:30px;background:var(--blue);color:var(--white);font-size:15px;text-align:center;line-height:30px}

.panels{top:590px;display:grid;grid-template-columns:repeat(3,288px);gap:37px}
.panel{height:339px;border:1px solid var(--rule);border-radius:3px;padding:18px 20px 0 21px}
.panel-head{display:flex;align-items:center;gap:18px;height:47px;margin-bottom:14px}
.panel-head::after{content:none}
.panel-icon{width:47px;height:47px;border-radius:50%;background:var(--blue);flex:none;display:flex;align-items:center;justify-content:center}
.panel-title{font-size:26px;font-weight:700;color:var(--blue);letter-spacing:.2px}
.panel-rule{height:1px;background:var(--rule);margin-bottom:12px}
.panel p{font-size:12.3px;line-height:26.2px;color:var(--ink);margin-bottom:26px}
.services{list-style:none;font-size:12.8px;line-height:26.2px}
.services li{display:flex;align-items:center;gap:12px}
.sub{font-size:13.5px;color:var(--blue);margin:0 0 6px 1px}
.contact-note{font-size:11.5px;line-height:22.5px;margin-bottom:30px}
.contact-note, .contact-list{color:var(--ink)}
.contact-list{list-style:none;font-size:12.5px;line-height:22.5px}
.contact-list li{display:flex;gap:13px}
.contact-list svg{flex:none;margin-top:7px}
.contact-list .indent{padding-left:24px}

.site-footer{position:absolute;left:0;top:975px;width:1200px;height:113px;background:var(--blue)}
.social{position:absolute;left:507px;top:-21px;display:flex;gap:1px}
.social span{width:37px;height:37px;border-radius:50%;background:var(--white);border:3px solid var(--blue);display:block;position:relative}
.social span::after{content:"";position:absolute;inset:6px;border-radius:50%;background:var(--blue)}
.footer-links{position:absolute;top:44px;width:100%;text-align:center;font-size:13.5px;color:var(--white)}
.footer-links a{color:inherit;text-decoration:none}
.footer-links .sep{margin:0 10px}
.copyright{position:absolute;top:81px;width:100%;text-align:center;font-size:11.5px;color:#d9ecf7}
</style>
</head>
<body>
<div class="page">
  <header class="wrap site-header">
    <div class="brand"><span class="brand-dot"></span><span class="brand-name">Velun Tresk, PLLC</span></div>
    <div class="header-contact">
      <svg width="16" height="20" viewBox="0 0 16 20" aria-hidden="true"><path d="M3 1l3 1-1 4-2 1c1 4 3 7 6 9l2-2 4 2-1 3c-2 1-5 0-8-3S0 7 1 3z" fill="#8a8a8a"/></svg>
      <span class="phone">555-208-3194</span>
      <svg width="14" height="20" viewBox="0 0 14 20" aria-hidden="true"><path d="M7 0a7 7 0 0 1 7 7c0 5-7 13-7 13S0 12 0 7a7 7 0 0 1 7-7z" fill="#8a8a8a"/><circle cx="7" cy="7" r="2.6" fill="#fff"/></svg>
      <span class="map-link">Map</span>
    </div>
    <nav class="main-nav" style="width:538px;height:22px">
      <a class="current" style="left:0">Home</a>
      <a style="left:62px">About Us</a>
      <a style="left:165px">Firm</a>
      <a style="left:212px">Media &amp; Events</a>
      <a style="left:334px">Practices</a>
      <a style="left:416px">FAQs</a>
      <a style="left:467px">Contact Us</a>
    </nav>
  </header>

  <section class="wrap hero">
    <div class="hero-photo" role="img" aria-label="Photo of a smiling lawyer in a dark suit in an office, with colleagues and a brass scale of justice on a desk"></div>
    <div class="hero-caption">
      <p>We like solving your problems when they happen but love<br>anticipating them so they don’t.</p>
      <a class="btn">Read More</a>
    </div>
  </section>

  <main class="wrap panels">
    <article class="panel">
      <div class="panel-head">
        <span class="panel-icon"><svg width="22" height="30" viewBox="0 0 22 30"><path d="M3 9a8 8 0 1 1 12 6c-2 1-2 2-2 4v1H8v-2c0-3 1-4 3-5 2-1 3-2 3-4a3 3 0 0 0-6 0z" fill="#fff"/><rect x="8" y="23" width="5" height="5" fill="#fff"/></svg></span>
        <h2 class="panel-title">WHY US</h2>
      </div>
      <div class="panel-rule"></div>
      <p>Lid est laborum dolo rumes fugats untras. Eth arums ser quidem rerum facilis dolores nemis omnis fugats vitaes nemo minima rerums uns ers sadips amets.</p>
      <p>Lid est laborum dolo rumes fugats untras. Eth arums ser quidem rerum facilis dolores nemis omnis fugats vitaes nemo minima rerums uns ers sadips amets.</p>
    </article>

    <article class="panel">
      <div class="panel-head">
        <span class="panel-icon"><svg width="28" height="28" viewBox="0 0 28 28"><circle cx="10" cy="18" r="6" fill="none" stroke="#fff" stroke-width="4" stroke-dasharray="3 2"/><circle cx="19" cy="8" r="4" fill="none" stroke="#fff" stroke-width="3" stroke-dasharray="2 1.5"/></svg></span>
        <h2 class="panel-title">WHAT WE DO</h2>
      </div>
      <div class="panel-rule"></div>
      <ul class="services">
        <li><svg width="12" height="10" viewBox="0 0 12 10"><path d="M1 5l3 3 7-7" fill="none" stroke="#0e87c8" stroke-width="2"/></svg>Intellectual Property</li>
        <li><svg width="12" height="10" viewBox="0 0 12 10"><path d="M1 5l3 3 7-7" fill="none" stroke="#0e87c8" stroke-width="2"/></svg>Patents</li>
        <li><svg width="12" height="10" viewBox="0 0 12 10"><path d="M1 5l3 3 7-7" fill="none" stroke="#0e87c8" stroke-width="2"/></svg>Copyrights</li>
        <li><svg width="12" height="10" viewBox="0 0 12 10"><path d="M1 5l3 3 7-7" fill="none" stroke="#0e87c8" stroke-width="2"/></svg>Trademarks</li>
        <li><svg width="12" height="10" viewBox="0 0 12 10"><path d="M1 5l3 3 7-7" fill="none" stroke="#0e87c8" stroke-width="2"/></svg>Trade secrets</li>
        <li><svg width="12" height="10" viewBox="0 0 12 10"><path d="M1 5l3 3 7-7" fill="none" stroke="#0e87c8" stroke-width="2"/></svg>Healthcare Compliance</li>
        <li><svg width="12" height="10" viewBox="0 0 12 10"><path d="M1 5l3 3 7-7" fill="none" stroke="#0e87c8" stroke-width="2"/></svg>Elder law</li>
        <li><svg width="12" height="10" viewBox="0 0 12 10"><path d="M1 5l3 3 7-7" fill="none" stroke="#0e87c8" stroke-width="2"/></svg>Wills</li>
        <li><svg width="12" height="10" viewBox="0 0 12 10"><path d="M1 5l3 3 7-7" fill="none" stroke="#0e87c8" stroke-width="2"/></svg>Trusts</li>
      </ul>
    </article>

    <article class="panel">
      <div class="panel-head">
        <span class="panel-icon"><svg width="28" height="24" viewBox="0 0 28 24"><path d="M2 10l12-8 12 8v12H2z" fill="none" stroke="#fff" stroke-width="2"/><rect x="7" y="6" width="14" height="9" fill="#fff"/><path d="M2 10l12 8 12-8" fill="none" stroke="#fff" stroke-width="2"/></svg></span>
        <h2 class="panel-title">CONTACT US</h2>
      </div>
      <div class="panel-rule"></div>
      <h3 class="sub">Say Hello!</h3>
      <p class="contact-note">Fusce dapibus, tellus commmcondimentum utellus fermalesuada magna. Fusce dapibus, tellus commmcondimentum......</p>
      <h3 class="sub">Address:</h3>
      <ul class="contact-list">
        <li><svg width="9" height="12" viewBox="0 0 9 12"><path d="M4.5 0A4.5 4.5 0 0 1 9 4.5C9 8 4.5 12 4.5 12S0 8 0 4.5A4.5 4.5 0 0 1 4.5 0z" fill="#777"/><circle cx="4.5" cy="4.5" r="1.6" fill="#fff"/></svg>Harrow Lane No: 22/07</li>
        <li class="indent">Brinford, Cassia</li>
        <li><svg width="11" height="9" viewBox="0 0 11 9"><path d="M0 3c3-3 8-3 11 0l-2 1-1-1H3L2 4z M2 5h7v4H2z" fill="#777"/></svg>0381 662 04 19</li>
        <li><svg width="11" height="8" viewBox="0 0 11 8"><rect width="11" height="8" fill="#777"/><path d="M0 0l5.5 4L11 0" fill="none" stroke="#fff"/></svg>Office@tresklaw.Example</li>
      </ul>
    </article>
  </main>

  <footer class="site-footer">
    <div class="social" aria-label="Social links"><span></span><span></span><span></span><span></span><span></span></div>
    <div class="footer-links"><a>Privacy Policy</a><span class="sep">|</span><a>Terms of Use</a><span class="sep">|</span><a>Site Map</a><span class="sep">|</span><a>Disclaimer</a></div>
    <div class="copyright">20014 © Copyright&nbsp; All Rights Reserved</div>
  </footer>
</div>
</body>
</html>
```